Honey Company from Florida Needs Sweet and Buzz-worthy Site

Website Requests:
-Deluxe 5-Page Website with SSL-Secure Online Store (Shopify)
-High-end imagery to appeal to a discerning consumer
-Detailed verbiage with strong SEO and easy readability
-Design principles: simple, chic, luxe, earthy
Pages:
1. Home {Local, Raw American Honey from Florida}
2. The Hive
> About Us
>Meet the Beekeepers
3. Buy Honey
> Shopify retail store
4. The Buzz {News, Recipes & More}
> Blog
5. Contact Us {We're Buzzin' to Meet You}
> Store Hours
> Phone Number
> Address
> Quick Contact Form
Attachments: Web design notes, Logo, Color Codes, Inspiration Photos
Target Market(s)
High-end honey consumer in the U.S.
Industry/Entity Type
Upscale honey enthusiasts; direct to consumer sales.
Coding
Coded - Design and coding required
Number of Pages Required
5+ page
Requirements
Must have
- Upscale look and feel, easy usability for quick sales.

```html
<!DOCTYPE html>
<html lang="en">
<head>
<meta charset="utf-8">
<title>Golden Comb Company — Raw Florida Honey</title>
<link href="https://fonts.googleapis.com/css2?family=Roboto+Slab:wght@700;800&family=Roboto:wght@400;500;700&display=swap" rel="stylesheet">
<style>
:root{
  --gold:#e8c04d;
  --gold-deep:#d9ab2e;
  --ink:#1f1f1f;
  --text:#333;
  --muted:#7a7a7a;
  --panel:#eceef1;
  --dark:#1d1d1d;
  --line:#e2e2e2;
  --white:#fff;
}
*{box-sizing:border-box;margin:0;padding:0}
html,body{width:1200px;height:3641px;overflow:hidden}
body{font-family:"Roboto",Arial,sans-serif;color:var(--text);background:var(--white)}
a{color:inherit;text-decoration:none}
.wrap{width:976px;margin:0 auto;position:relative}
.slab{font-family:"Roboto Slab",Georgia,serif;font-weight:800;letter-spacing:.5px;color:var(--ink)}
.btn{display:inline-flex;align-items:center;justify-content:center;background:var(--gold);color:var(--ink);font-weight:700;font-size:16px;border-radius:3px;text-transform:uppercase}

/* header */
.site-header{height:94px;display:flex;align-items:center}
.site-header .wrap{display:flex;align-items:center;justify-content:space-between}
.brand{display:flex;align-items:center;gap:10px;font-weight:700;font-size:17px;color:var(--ink)}
.brand-dot{width:40px;height:40px;border-radius:50%;border:2px solid var(--ink)}
.main-nav{display:flex;gap:26px;font-size:15px;font-weight:500;color:var(--ink);margin-left:80px}
.header-icons{display:flex;gap:10px}
.header-icons span{width:32px;height:32px;border:2px solid var(--ink);border-radius:50%;display:flex;align-items:center;justify-content:center}

/* hero */
.hero{height:582px;position:relative;background:linear-gradient(100deg,#3d2a14 0%,#6b4a22 35%,#8a5a1c 55%,#a8581a 75%,#5a3515 100%)}
.hero-copy{position:absolute;left:112px;top:272px;color:var(--white)}
.hero-copy h1{font-family:"Roboto Slab",Georgia,serif;font-weight:800;font-size:40px;color:var(--white);letter-spacing:.5px}
.hero-copy p{font-size:16px;font-weight:500;line-height:28px;margin-top:16px;width:520px}
.hero-copy .btn{width:140px;height:46px;margin-top:24px}

/* about */
.about{height:648px;position:relative}
.hexagon{position:absolute;left:112px;top:104px;width:488px;height:425px;clip-path:polygon(25% 0,75% 0,100% 50%,75% 100%,25% 100%,0 50%);background:linear-gradient(135deg,#b8945a,#7a5a2e 50%,#c9a868)}
.about-copy{position:absolute;left:651px;top:94px;width:440px}
.about-copy h2{font-size:34px;line-height:42px}
.bullets{list-style:none;margin-top:30px}
.bullets li{position:relative;padding-left:29px;font-size:14px;line-height:26px;color:#555;margin-bottom:8px}
.bullets svg{position:absolute;left:0;top:7px}
.about-copy .btn{width:138px;height:44px;font-size:14px;color:var(--white);margin-top:30px;text-transform:uppercase}

/* shop */
.shop{height:535px;background:var(--panel)}
.section-title{font-size:40px;text-align:center;padding-top:56px}
.products{display:flex;gap:17px;margin-top:38px}
.product{width:231px}
.product-img{height:233px;border-radius:2px}
.product h3{font-size:16px;font-weight:500;color:var(--ink);margin-top:22px}
.price{margin-top:12px;font-weight:700;font-size:16px;color:var(--gold)}
.price s{font-weight:400;font-size:12px;margin-left:8px}

/* health */
.health{height:458px;display:flex}
.health-copy{width:623px;background:var(--dark);padding:50px 46px 0 112px;color:#eee}
.health-copy h2{font-family:"Roboto Slab",Georgia,serif;font-weight:800;font-size:38px;line-height:46px;color:var(--white)}
.health-copy p{font-size:14px;line-height:27.5px;margin-top:24px;text-align:justify}
.health-copy .btn{width:127px;height:44px;font-size:14px;margin-top:24px}
.health-img{flex:1;background:linear-gradient(135deg,#2a2a2a,#1a1a1a 45%,#c9a12a 70%,#2a2a2a)}

/* buzz */
.buzz{height:618px}
.buzz .section-title{padding-top:88px}
.posts{display:flex;gap:20px;margin-top:36px}
.post{width:312px}
.post-img{height:242px}
.post h3{font-size:16px;font-weight:700;color:var(--ink);margin-top:26px}
.post p{font-size:14px;line-height:22px;color:var(--muted);margin-top:12px}

/* gallery */
.gallery{height:429px;display:flex}
.gallery div{flex:1}

/* footer */
.site-footer{height:207px}
.footer-top{display:flex;padding-top:72px}
.footer-col h4{font-size:16px;font-weight:700;color:var(--ink)}
.quick{width:502px}
.quick nav{display:flex;gap:26px;font-size:14px;color:var(--muted);margin-top:20px}
.newsletter form{display:flex;margin-top:18px}
.newsletter input{width:363px;height:39px;border:1px solid var(--line);border-right:none}
.newsletter button{width:111px;height:39px;border:none;background:var(--gold);color:var(--white);font-weight:700;font-size:16px;font-family:inherit}
.footer-bottom{border-top:1px solid var(--line);margin-top:50px;height:70px;display:flex;align-items:center}
.footer-bottom .wrap{display:flex;align-items:center;justify-content:space-between}
.cards{display:flex;gap:4px}
.cards span{width:30px;height:17px;border-radius:2px;background:#c7ccd6}
.copyright{font-size:14px;color:var(--muted)}
.social{display:flex;gap:10px}
.social span{width:32px;height:32px;border:1.5px solid #555;border-radius:50%}
</style>
</head>
<body>

<header class="site-header">
  <div class="wrap">
    <a class="brand" href="#"><span class="brand-dot"></span>Golden Comb Company</a>
    <nav class="main-nav">
      <a href="#">Home</a><a href="#">The Hive</a><a href="#">Buy Honey</a><a href="#">The Buzz</a><a href="#">Contact</a>
    </nav>
    <div class="header-icons">
      <span><svg width="14" height="14" viewBox="0 0 14 14"><circle cx="6" cy="6" r="4" fill="none" stroke="#1f1f1f" stroke-width="2"/><path d="M9 9l3.5 3.5" stroke="#1f1f1f" stroke-width="2"/></svg></span>
      <span><svg width="14" height="14" viewBox="0 0 14 14"><circle cx="7" cy="4.5" r="3" fill="#1f1f1f"/><path d="M1.5 13a5.5 5.5 0 0 1 11 0z" fill="#1f1f1f"/></svg></span>
      <span><svg width="14" height="14" viewBox="0 0 14 14"><path d="M1 2h2l2 7h7l1.5-5H4" fill="none" stroke="#1f1f1f" stroke-width="1.8"/><circle cx="6" cy="12" r="1.2" fill="#1f1f1f"/><circle cx="11" cy="12" r="1.2" fill="#1f1f1f"/></svg></span>
    </div>
  </div>
</header>

<section class="hero" role="img" aria-label="Honey dipper dripping into a glass jar of amber honey beside honeycomb pieces on a wooden table">
  <div class="hero-copy">
    <h1>BLESSED TO BEE-KEEP</h1>
    <p>100% raw, unfiltered Florida honey straight from he beehives on his six-acre property, Golden Comb Honey Farm, 32190</p>
    <a class="btn" href="#">Shop Now</a>
  </div>
</section>

<section class="about">
  <div class="hexagon" role="img" aria-label="Beekeeper in protective suit lifting a honeycomb frame from a hive"></div>
  <div class="about-copy">
    <h2 class="slab">DON’T JUDGE A BEE BY ITS STINGER</h2>
    <ul class="bullets">
      <li><svg width="14" height="14" viewBox="0 0 14 14"><circle cx="7" cy="7" r="7" fill="#e8c04d"/><path d="M4 7.2l2 2 4-4" fill="none" stroke="#fff" stroke-width="1.6"/></svg>Hyper-efficient insects do play a vital role in agriculture. Almonds, for example, are almost entirely dependent on honeybee pollination.</li>
      <li><svg width="14" height="14" viewBox="0 0 14 14"><circle cx="7" cy="7" r="7" fill="#e8c04d"/><path d="M4 7.2l2 2 4-4" fill="none" stroke="#fff" stroke-width="1.6"/></svg>“Over one-third of our entire diet is dependent on pollination from the honeybee. So, for every three bites of food you eat, you can thank the honeybee for one of those three bites,” Walter says.</li>
      <li><svg width="14" height="14" viewBox="0 0 14 14"><circle cx="7" cy="7" r="7" fill="#e8c04d"/><path d="M4 7.2l2 2 4-4" fill="none" stroke="#fff" stroke-width="1.6"/></svg>They are very misunderstood among the public. We have lost a great amount of our natural forage land due to</li>
    </ul>
    <a class="btn" href="#">Learn More</a>
  </div>
</section>

<section class="shop">
  <div class="wrap">
    <h2 class="slab section-title">BUY HONEY</h2>
    <div class="products">
      <div class="product"><div class="product-img" role="img" aria-label="Hexagonal honey gift boxes in gold and brown" style="background:linear-gradient(135deg,#fff,#e9dcc0 50%,#8a5a22)"></div><h3>Lorem ipsum dolor sit</h3><p class="price">$35.99</p></div>
      <div class="product"><div class="product-img" role="img" aria-label="Honey jar with bee-print label beside an open white gift box" style="background:linear-gradient(135deg,#3a3a3a,#6a6a6a 50%,#e2d3b0)"></div><h3>Lorem ipsum dolor sit</h3><p class="price">$16.79</p></div>
      <div class="product"><div class="product-img" role="img" aria-label="Honey bottle in a wooden honeycomb-patterned frame box" style="background:linear-gradient(135deg,#f2f2f2,#c9a26a 50%,#6a3a1a)"></div><h3>Lorem ipsum dolor sit</h3><p class="price">$20.79 <s>$25.99</s></p></div>
      <div class="product"><div class="product-img" role="img" aria-label="Three honey jars with a wooden dipper in a kraft gift box" style="background:linear-gradient(180deg,#d9dadc,#c8a66a 40%,#5a3a1a)"></div><h3>Lorem ipsum dolor sit</h3><p class="price">$24.99</p></div>
    </div>
  </div>
</section>

<section class="health">
  <div class="health-copy">
    <h2>THE HEALTH BENEFITS OF HONEY</h2>
    <p>Raw honey is loaded with antioxidants to protect your body from cell damage due to free radicals. Honey has been long known as a folk remedy to help heal burns and wounds due to its antibacterial and antifungal properties. Honey is also very well known to soothe a sore throat. Try taking a spoonful of honey and add it to hot tea if you feel like you have a cold. Honey can also help as a cough suppressant.</p>
    <a class="btn" href="#">Shop Now</a>
  </div>
  <div class="health-img" role="img" aria-label="Black and gold honey gift boxes holding jars and wooden spoons on yellow trays"></div>
</section>

<section class="buzz">
  <div class="wrap">
    <h2 class="slab section-title">THE BUZZ</h2>
    <div class="posts">
      <div class="post"><div class="post-img" role="img" aria-label="Creamed honey in a white bowl with a silver spoon on a dark surface" style="background:linear-gradient(135deg,#2a2a2a,#c99a3a 50%,#1e1e1e)"></div><h3>Lorem ipsum dolor sit amet</h3><p>Sed ut perspiciatis unde omnis iste natus error sit voluptatem accusantium</p></div>
      <div class="post"><div class="post-img" role="img" aria-label="Honey drizzled from a spoon into a small bowl above fresh berries" style="background:linear-gradient(160deg,#3a4a2a,#e8e2d8 50%,#9a2a3a)"></div><h3>Lorem ipsum dolor sit amet</h3><p>Sed ut perspiciatis unde omnis iste natus error sit voluptatem accusantium</p></div>
      <div class="post"><div class="post-img" role="img" aria-label="Hands drizzling honey over a bowl of yogurt with a glass of tea" style="background:linear-gradient(135deg,#2e4a3a,#5a7a5a 50%,#3a3020)"></div><h3>Lorem ipsum dolor sit amet</h3><p>Sed ut perspiciatis unde omnis iste natus error sit voluptatem accusantium</p></div>
    </div>
  </div>
</section>

<section class="gallery">
  <div role="img" aria-label="Black and gold honey gift boxes with jars" style="background:linear-gradient(135deg,#222,#c9a12a 55%,#1a1a1a)"></div>
  <div role="img" aria-label="Kraft gift box with three honey jars and a dipper" style="background:linear-gradient(180deg,#e6e6e6,#c8a66a 45%,#5a3a1a)"></div>
  <div role="img" aria-label="Bee-print honey jar beside an open gift box" style="background:linear-gradient(135deg,#3a3a3a,#5e5e5e 50%,#e6d8b8)"></div>
</section>

<footer class="site-footer">
  <div class="wrap footer-top">
    <div class="footer-col quick">
      <h4>Quick Links</h4>
      <nav><a href="#">Home</a><a href="#">Products</a><a href="#">About US</a><a href="#">FAQ</a><a href="#">Support</a><a href="#">Reviews</a></nav>
    </div>
    <div class="footer-col newsletter">
      <h4>Newsletter</h4>
      <form><input type="email" aria-label="Email address"><button type="button">Subscribe</button></form>
    </div>
  </div>
  <div class="footer-bottom">
    <div class="wrap">
      <div class="cards"><span></span><span></span><span></span><span></span><span></span></div>
      <p class="copyright">© 2021 GoldenComb | All Rights Reserved</p>
      <div class="social"><span></span><span></span><span></span><span></span></div>
    </div>
  </div>
</footer>

</body>
</html>
```